New Business Card Design

We need a business card design for a new company based in Sydney called "Haven and Hue". This is an online buisness which will have an online store providing imported homewares.
We are looking for something that is different, perhaps even in shape and using the logo that was designed by Pixel Harbor.

Attached document is a basic example I want to see more creative versions.

Target Market(s)

Homewares, Interior Design

Industry/Entity Type

Business

Contact Information for Business Card

Company Logo
Company Name
Industry area
Name
Position
Phone
Email
Website
Motto

Requirements
Must have
• Logo
Nice to have
• Social website logos - Chatterloop, Glimmoraly, Quibbly, Boardlyne, Veltrix+

```html
<!DOCTYPE html>
<html lang="en">
<head>
<meta charset="utf-8">
<title>Haven and Hue – Business Card</title>
<link rel="stylesheet" href="https://fonts.googleapis.com/css2?family=Montserrat:wght@400;500;700&family=Open+Sans:wght@400;700&family=Roboto+Condensed:wght@700&family=Pinyon+Script&display=swap">
<style>
  :root {
    --backdrop: #a8a6a7;
    --card: #ffffff;
    --ink: #1c1c1c;
    --text: #2a2a2a;
    --gold: #a8825c;
    --gold-light: #f3e2b0;
    --gold-mid: #c49a55;
    --bronze: #7e5236;
    --black: #161616;
  }
  * { margin: 0; padding: 0; box-sizing: border-box; }
  html, body { width: 1200px; height: 1200px; overflow: hidden; }
  body { background: var(--backdrop); position: relative; font-family: "Open Sans", sans-serif; color: var(--text); }

  .card {
    position: absolute;
    width: 716px;
    height: 416px;
    background: var(--card);
    border-radius: 22px;
    overflow: hidden;
  }
  .card--front { left: 236px; top: 120px; }
  .card--back { left: 232px; top: 645px; }

  .gold-band { fill: url(#goldSheen); }
  .card svg.band { position: absolute; left: 0; top: 0; width: 716px; height: 416px; }

  /* Front */
  .front-brand {
    position: absolute; left: 0; right: 0; top: 118px;
    text-align: center;
    font-family: "Montserrat", sans-serif; font-weight: 500;
    font-size: 52px; color: var(--ink);
  }
  .front-industry {
    position: absolute; left: 0; right: 0; top: 288px;
    text-align: center;
    font-family: "Montserrat", sans-serif; font-weight: 400;
    font-size: 37px; letter-spacing: 0.09em; color: var(--ink);
  }
  .front-web {
    position: absolute; left: 0; right: 0; top: 341px;
    display: flex; align-items: center; justify-content: center; gap: 10px;
    font-size: 17px; color: var(--text);
  }
  .front-web .rule { width: 90px; height: 2px; background: linear-gradient(90deg, transparent, var(--gold-mid)); }
  .front-web .rule--right { background: linear-gradient(90deg, var(--gold-mid), transparent); }

  /* Back */
  .brand-mark {
    position: absolute; left: 70px; top: 36px;
    width: 112px; height: 112px; border-radius: 50%;
    background: var(--black);
  }
  .brand-name {
    position: absolute; left: 226px; top: 50px;
    font-family: "Montserrat", sans-serif; font-weight: 700;
    font-size: 36px; color: var(--ink);
  }
  .brand-industry {
    position: absolute; left: 228px; top: 98px;
    font-family: "Montserrat", sans-serif; font-weight: 400;
    font-size: 24px; letter-spacing: 0.95em; color: var(--ink);
  }
  .person-name {
    position: absolute; left: 42px; top: 176px;
    font-family: "Roboto Condensed", sans-serif; font-weight: 700;
    font-size: 28px; color: var(--gold);
  }
  .person-role { position: absolute; left: 42px; top: 216px; font-size: 17px; }

  .social-list { position: absolute; left: 42px; top: 260px; list-style: none; }
  .social-list li { display: flex; align-items: center; gap: 14px; height: 25.5px; font-size: 17px; }
  .social-list .dot { width: 16px; height: 16px; border-radius: 3px; background: var(--gold); }

  .contact-list { position: absolute; left: 356px; top: 210px; list-style: none; }
  .contact-list li { display: flex; align-items: center; gap: 14px; height: 29.5px; font-size: 17px; }
  .contact-list svg { width: 18px; height: 18px; fill: var(--gold); }
  .contact-list .web { font-weight: 700; font-size: 19px; color: var(--ink); }

  .motto {
    position: absolute; left: 356px; top: 370px;
    font-family: "Pinyon Script", cursive; font-size: 27px;
    color: #fff8ea;
  }
</style>
</head>
<body>
  <svg width="0" height="0" style="position:absolute">
    <defs>
      <linearGradient id="goldSheen" x1="0" x2="1" y1="0" y2="0">
        <stop offset="0" stop-color="#a97d43"/>
        <stop offset="0.25" stop-color="#f3e2b0"/>
        <stop offset="0.45" stop-color="#7e5236"/>
        <stop offset="0.7" stop-color="#f5e6bf"/>
        <stop offset="1" stop-color="#c49a55"/>
      </linearGradient>
      <linearGradient id="goldMotto" x1="0" x2="1" y1="0" y2="0">
        <stop offset="0" stop-color="#e8cf93"/>
        <stop offset="0.4" stop-color="#b98a4e"/>
        <stop offset="1" stop-color="#6f4530"/>
      </linearGradient>
    </defs>
  </svg>

  <section class="card card--front">
    <div class="front-brand">Haven and Hue</div>
    <div class="front-industry">HOMEWARES</div>
    <div class="front-web"><span class="rule"></span>www.havenandhue.com.au<span class="rule rule--right"></span></div>
    <svg class="band" viewBox="0 0 716 416">
      <polygon points="502,398 716,398 716,416 488,416" fill="#161616"/>
      <polygon class="gold-band" points="0,398 506,398 478,416 0,416"/>
    </svg>
  </section>

  <section class="card card--back">
    <div class="brand-mark"></div>
    <div class="brand-name">Haven and Hue</div>
    <div class="brand-industry">Homewares</div>

    <div class="person-name">Marisol Everly Dunn</div>
    <div class="person-role">Director / Designer</div>

    <ul class="social-list">
      <li><span class="dot"></span>havenandhue</li>
      <li><span class="dot"></span>havenandhue</li>
      <li><span class="dot"></span>@HavenAndHue1</li>
      <li><span class="dot"></span>havenandhuehomewares</li>
    </ul>

    <ul class="contact-list">
      <li><svg viewBox="0 0 24 24"><path d="M3 8c0-2 2-4 9-4s9 2 9 4v2h-5V8H8v2H3zM6 11h12l2 8H4z"/></svg>+61 400 555 017</li>
      <li><svg viewBox="0 0 24 24"><path d="M2 5h20v14H2zM4 7v1l8 5 8-5V7l-8 5z" fill-rule="evenodd"/></svg>marisol@havenandhue.com.au</li>
      <li><svg viewBox="0 0 24 24"><circle cx="12" cy="12" r="9" fill="none" stroke="#a8825c" stroke-width="2"/><ellipse cx="12" cy="12" rx="4" ry="9" fill="none" stroke="#a8825c" stroke-width="1.6"/><path d="M3 12h18M5 7h14M5 17h14" stroke="#a8825c" stroke-width="1.4"/></svg><span class="web">www.havenandhue.com.au</span></li>
    </ul>

    <svg class="band" viewBox="0 0 716 416">
      <polygon points="0,389 330,389 322,416 0,416" fill="#161616"/>
      <polygon points="340,363 716,363 716,416 308,416" fill="url(#goldMotto)"/>
    </svg>
    <div class="motto">Adding Style to your Home</div>
  </section>
</body>
</html>
```